Singer/Songwriter/performer wants Retro Art Poster

I'm looking for a beautiful iconic art poster design that incorporates an image of me, my name and possibly a quote...could be a heavily treated image or an illustration. Something that people will want to put on their walls in their homes. Could have a vintage vibe like the Red Harbor record label Jazz posters.It could include a press quote ... you can find high res images to use and more information about me with music here https://lisarichardsmusic.com/epk-bioI've included a couple of examples... But I'm open to other ideas. Musically ... here's a description of what I do.."With an instantly identifiable vocal timbre and an elastic sense of phrasing, Moira has been called a singer's singer. Her songs are a melting pot mixture of jazz, folk, blues, pop, rock and country - her own brand of adventurous folk art.. She's released 6 albums and is working on her 7th."
People who enjoy my music and want to buy something that represents what I do that isn't actual music
Designer to choose colors to be used in the design.

```html
<!DOCTYPE html>
<html lang="en">
<head>
<meta charset="utf-8">
<title>Moira Dunne – We need each other</title>
<link rel="stylesheet" href="https://fonts.googleapis.com/css2?family=Fraunces:opsz,wght@144,900&family=Oswald:wght@700&display=swap">
<style>
  :root {
    --navy: #08263d;
    --cream: #e6f0c0;
    --mint: #8ff5d0;
    --slate: #455f66;
    --photo-light: #6fcfb5;
    --photo-dark: #17352f;
  }
  html, body {
    margin: 0;
    padding: 0;
    width: 800px;
    height: 1200px;
    overflow: hidden;
    background: var(--cream);
  }
  .poster {
    position: relative;
    width: 800px;
    height: 1200px;
    overflow: hidden;
    background: var(--cream);
  }
  .poster-art {
    position: absolute;
    inset: 0;
    display: block;
  }
  .headline {
    font-family: "Fraunces", "Cooper Black", serif;
    font-weight: 900;
    font-size: 118px;
  }
  .headline--light { fill: var(--cream); }
  .headline--dark { fill: var(--navy); }
  .drop--navy { fill: var(--navy); }
  .drop--slate { fill: var(--slate); }
  .drop--mint { fill: var(--mint); opacity: 0.75; }
  .top-band { fill: var(--navy); }
  .artist-name {
    position: absolute;
    left: 24px;
    top: 1090px;
    margin: 0;
    font-family: "Oswald", "Arial Narrow", sans-serif;
    font-weight: 700;
    color: var(--navy);
    line-height: 1;
  }
  .artist-name__first {
    display: block;
    font-size: 40px;
    letter-spacing: 14px;
  }
  .artist-name__last {
    display: block;
    font-size: 44px;
    letter-spacing: 1px;
  }
</style>
</head>
<body>
<main class="poster">
  <svg class="poster-art" width="800" height="1200" viewBox="0 0 800 1200" xmlns="http://www.w3.org/2000/svg">
    <defs>
      <symbol id="drop" viewBox="0 0 100 160" preserveAspectRatio="none">
        <path d="M50 0 C65 35 100 75 100 110 A50 50 0 0 1 0 110 C0 75 35 35 50 0 Z"/>
      </symbol>
      <linearGradient id="photo-tone" x1="0" y1="0" x2="0" y2="1">
        <stop offset="0" stop-color="var(--photo-light)"/>
        <stop offset="1" stop-color="var(--photo-dark)"/>
      </linearGradient>
    </defs>

    <!-- top band with hanging drops -->
    <path class="top-band" d="M0 0 H800 V360 Q800 392 770 390 C600 380 420 330 230 318 C120 312 40 330 0 345 Z"/>
    <use class="drop--navy" href="#drop" x="149" y="300" width="92" height="125"/>
    <use class="drop--navy" href="#drop" x="282" y="365" width="32" height="65"/>
    <use class="drop--navy" href="#drop" x="701" y="385" width="64" height="107"/>

    <!-- headline -->
    <text class="headline headline--light" x="220" y="128" textLength="520" lengthAdjust="spacingAndGlyphs">We need</text>
    <text class="headline headline--light" x="30" y="252" textLength="738" lengthAdjust="spacingAndGlyphs">each other...</text>
    <text class="headline headline--dark" x="20" y="508" textLength="640" lengthAdjust="spacingAndGlyphs">like water</text>
    <text class="headline headline--dark" x="20" y="628" textLength="762" lengthAdjust="spacingAndGlyphs">needs to fall</text>

    <!-- falling drops behind the portrait -->
    <use class="drop--navy" href="#drop" x="154" y="640" width="32" height="55"/>
    <use class="drop--navy" href="#drop" x="440" y="645" width="94" height="158"/>
    <use class="drop--navy" href="#drop" x="53" y="728" width="64" height="105"/>
    <use class="drop--slate" href="#drop" x="152" y="838" width="32" height="52"/>
    <use class="drop--slate" href="#drop" x="14" y="880" width="94" height="160"/>
    <use class="drop--navy" href="#drop" x="101" y="1035" width="32" height="55"/>

    <!-- portrait photo area -->
    <rect class="portrait" role="img"
          aria-label="Duotone photograph of the singer in a pinstripe suit, head tilted back, playing an acoustic guitar"
          x="200" y="665" width="490" height="535" fill="url(#photo-tone)"/>

    <!-- drops over the portrait -->
    <use class="drop--mint" href="#drop" x="46" y="710" width="46" height="80"/>
    <use class="drop--mint" href="#drop" x="503" y="722" width="64" height="110"/>
    <use class="drop--navy" href="#drop" x="674" y="700" width="32" height="55"/>
    <use class="drop--mint" href="#drop" x="684" y="713" width="64" height="122"/>
    <use class="drop--slate" href="#drop" x="597" y="797" width="64" height="103"/>
    <use class="drop--mint" href="#drop" x="632" y="807" width="32" height="53"/>
    <use class="drop--navy" href="#drop" x="524" y="875" width="32" height="60"/>
    <use class="drop--mint" href="#drop" x="539" y="900" width="32" height="70"/>
    <use class="drop--mint" href="#drop" x="85" y="955" width="64" height="130"/>
    <use class="drop--navy" href="#drop" x="696" y="980" width="94" height="160"/>
    <use class="drop--mint" href="#drop" x="670" y="1100" width="32" height="65"/>
  </svg>

  <h1 class="artist-name">
    <span class="artist-name__first">MOIRA</span>
    <span class="artist-name__last">DUNNE</span>
  </h1>
</main>
</body>
</html>
```